Tallon Electrical Business Card

We need a business card design for our family-run electrical contracting business based in Western Australia called 'Tallon Electrical'. We provide electrical services including residential, commercial and industrial. We aim for individual business cards to be made for all of our employees. We already have a company logo, which we require to be featured on the design. We would like simple, sleek and vibrant designs, which incorporate our logo and represent our business. We do not want anything involving too many graphics/images. We like the colours red, black, white and all shades of grey. The final design should communicate professionalism and trustworthiness.
We require the following contact information:
Name- Grant Pellow
EC 5871
Mobile number- 0455 870 219
Fax number (including area code)- (08) 9560 2831
Email adress- name@tallonelectrical.com.au
Electrical
- ITC Handel Bold

```html
<!DOCTYPE html>
<html lang="en">
<head>
<meta charset="utf-8">
<title>Tallon Electrical Business Card</title>
<link rel="stylesheet" href="https://fonts.googleapis.com/css2?family=Roboto:wght@300;400;700;900&display=swap">
<style>
  :root {
    --red: #e3191f;
    --red-deep: #c81218;
    --black: #1a1a1a;
    --grey-text: #555555;
    --card-white: #f4f4f4;
    --backdrop: #9b9b9b;
    --divider: #c9c9c9;
  }
  * { box-sizing: border-box; margin: 0; padding: 0; }
  html, body {
    width: 1200px; height: 720px; overflow: hidden;
    background: var(--backdrop);
    font-family: "Roboto", Arial, sans-serif;
  }
  .canvas {
    position: relative; width: 1200px; height: 720px;
    display: flex; align-items: center; justify-content: center; gap: 60px;
  }
  .card {
    position: relative; width: 520px; height: 318px;
    box-shadow: 0 6px 18px rgba(0,0,0,0.25);
  }
  /* Front: contact side */
  .card--front { background: var(--card-white); }
  .person { position: absolute; left: 34px; top: 40px; }
  .person__name { color: var(--red); font-weight: 700; font-size: 17px; letter-spacing: 0.2px; }
  .person__role { color: var(--grey-text); font-weight: 400; font-size: 14px; margin-top: 2px; }
  .brand {
    position: absolute; right: 34px; top: 36px;
    display: flex; align-items: center; gap: 10px;
  }
  .brand__square { width: 22px; height: 22px; background: var(--red); }
  .brand__name { color: var(--black); font-weight: 900; font-size: 22px; letter-spacing: 0.5px; text-transform: uppercase; }
  .divider {
    position: absolute; left: 248px; top: 140px; height: 120px;
    border-left: 2px dotted var(--divider);
  }
  .contacts {
    position: absolute; left: 272px; top: 140px; list-style: none;
    color: var(--grey-text); font-size: 14px; line-height: 1.25;
  }
  .contacts li { display: flex; gap: 12px; margin-bottom: 4px; }
  .contacts svg { width: 13px; height: 13px; flex: none; margin-top: 2px; fill: var(--red); }
  .contacts .contacts__email { margin-left: -14px; margin-top: 14px; }
  /* Back: brand side */
  .card--back { background: var(--red); overflow: hidden; }
  .back__texture {
    position: absolute; inset: 0;
    background: linear-gradient(135deg, var(--red) 0%, var(--red-deep) 100%);
  }
  .back__brand {
    position: absolute; left: 0; right: 0; top: 104px;
    display: flex; align-items: center; justify-content: center; gap: 12px;
  }
  .back__square { width: 26px; height: 26px; background: #ffffff; }
  .back__name { color: #ffffff; font-weight: 900; font-size: 30px; letter-spacing: 0.5px; text-transform: uppercase; }
  .back__web {
    position: absolute; left: 0; right: 0; top: 214px; text-align: center;
    color: #ffffff; font-weight: 300; font-size: 20px;
  }
  .back__web strong { font-weight: 700; }
</style>
</head>
<body>
<main class="canvas">
  <section class="card card--front" aria-label="Business card front">
    <div class="person">
      <p class="person__name">Grant Pellow</p>
      <p class="person__role">Director</p>
    </div>
    <div class="brand">
      <span class="brand__square"></span>
      <span class="brand__name">Tallon Electrical</span>
    </div>
    <div class="divider"></div>
    <ul class="contacts">
      <li>
        <svg viewBox="0 0 12 16"><path d="M6 0a6 6 0 0 0-6 6c0 4.5 6 10 6 10s6-5.5 6-10a6 6 0 0 0-6-6zm0 8.5A2.5 2.5 0 1 1 6 3.5a2.5 2.5 0 0 1 0 5z"/></svg>
        <span>EC 5871, address<br>town here 6542U</span>
      </li>
      <li>
        <svg viewBox="0 0 12 16"><path d="M2 0h8a1.5 1.5 0 0 1 1.5 1.5v13A1.5 1.5 0 0 1 10 16H2a1.5 1.5 0 0 1-1.5-1.5v-13A1.5 1.5 0 0 1 2 0zm0 2v10h8V2z"/></svg>
        <span>0455 870 219</span>
      </li>
      <li>
        <svg viewBox="0 0 16 16"><path d="M4 0h8v5H4zM1 6h14v8H1zm3 2v2h8V8z"/></svg>
        <span>(08) 9560 2831</span>
      </li>
      <li>
        <svg viewBox="0 0 16 12"><path d="M0 0h16v12H0zm1.5 1.5L8 6.5l6.5-5z"/></svg>
        <span>name@tallonelectrical.com.au</span>
      </li>
    </ul>
  </section>

  <section class="card card--back" aria-label="Business card back">
    <div class="back__texture" role="img" aria-label="Repeating tone-on-tone red brand pattern"></div>
    <div class="back__brand">
      <span class="back__square"></span>
      <span class="back__name">Tallon Electrical</span>
    </div>
    <p class="back__web">www.<strong>tallonelectrical</strong>.com.au</p>
  </section>
</main>
</body>
</html>
```